Lantern Hollow Brewing Company New Website with Food Ordering

We need a wordpress-based website for a local brewery & pizza kitchen. The final design will have 6 primary pages: home page, order pizza, our beers, visit us, about us, merch store. The website must integrate with tillpoint for kitchens for online ordering for takeout and delivery. It will also a feature a selection of beers and help customers navigate to the brewery and find hours of operation. The existing website is lanternhollowbrew.example. This is a very old website.

Industry/Entity Type

Brewery and food service

Coding

Coded - Design and coding required

Number of Pages Required

5+ page

Font styles to use
Sans Serif

Requirements
Must have
• ability to integrate seamlessly with tillpoint for kitchens, 21+ age gate
Nice to have
• see attached pdf

```html
<!DOCTYPE html>
<html lang="en">
<head>
<meta charset="utf-8">
<title>Lantern Hollow Brewing Company</title>
<link rel="stylesheet" href="https://fonts.googleapis.com/css2?family=Barlow:wght@500;600;700&family=Arimo:wght@400&display=swap">
<style>
  :root {
    --red: #c8102e;
    --ink: #141414;
    --dark: #1b1b1b;
    --white: #ffffff;
    --yellow: #f2c020;
    --photo-warm: #5a2a22;
    --photo-deep: #2a1512;
    --pattern-tone: #2a2a2a;
  }
  * { box-sizing: border-box; margin: 0; padding: 0; }
  html, body { width: 731px; height: 1200px; overflow: hidden; background: var(--ink); }
  body { position: relative; font-family: "Barlow", sans-serif; color: var(--white); }
  .abs { position: absolute; }

  .site-header { position: absolute; left: 0; top: 0; width: 731px; height: 49px; background: var(--ink); z-index: 3; }
  .brand { position: absolute; left: 68px; top: 16px; font-weight: 700; font-size: 12px; letter-spacing: .02em; display: flex; align-items: center; gap: 5px; }
  .brand-mark { width: 14px; height: 14px; background: var(--red); }
  .main-nav a { position: absolute; top: 20px; font-size: 8px; font-weight: 500; color: var(--white); text-decoration: none; }
  .takeaway-icon { position: absolute; left: 492px; top: 14px; width: 21px; height: 21px; border: 1px solid var(--white); border-radius: 50%; }
  .btn-order-head { position: absolute; left: 569px; top: 12.5px; width: 94px; height: 25px; border-radius: 13px; background: var(--red); font-size: 8px; font-weight: 500; display: flex; align-items: center; justify-content: center; }

  .hero { position: absolute; left: 0; top: 49px; width: 731px; height: 416px; background: radial-gradient(ellipse at 45% 40%, #6b3327 0%, var(--photo-warm) 35%, var(--photo-deep) 100%); }
  .hero-shade { position: absolute; inset: 0; background: rgba(0,0,0,.35); }
  .hero-title { position: absolute; left: 0; top: 143px; width: 731px; text-align: center; font-size: 28px; font-weight: 700; line-height: 36px; }
  .hero-btn { position: absolute; top: 231px; width: 105px; height: 37px; border: 1px solid var(--white); border-radius: 3px; font-size: 9px; font-weight: 500; display: flex; align-items: center; justify-content: center; }
  .hero-arrow { position: absolute; top: 197px; width: 24px; height: 24px; border-radius: 50%; background: var(--white); }
  .promo-badge { position: absolute; left: 614px; top: 32px; width: 96px; height: 66px; background: var(--yellow); border-radius: 4px; }

  .intro { position: absolute; left: 0; top: 440px; width: 731px; height: 520px; background: var(--dark); }
  .pattern-area { position: absolute; background: var(--pattern-tone); }
  .intro-title { position: absolute; left: 68px; top: 577px; font-size: 24px; font-weight: 700; line-height: 33px; }
  .intro-title em { font-style: normal; color: var(--red); }
  .intro-text { position: absolute; left: 68px; top: 650px; width: 285px; font-family: "Arimo", sans-serif; font-size: 8px; line-height: 17px; }
  .btn { position: absolute; top: 732px; width: 130px; height: 34px; border-radius: 17px; font-size: 9px; font-weight: 600; display: flex; align-items: center; justify-content: center; }
  .btn-solid { left: 68px; background: var(--red); }
  .btn-ghost { left: 205px; border: 1px solid var(--white); }
  .pizza-photo { position: absolute; left: 397px; top: 531px; width: 265px; height: 289px; border-radius: 21px; border: 1.5px solid var(--white); background: radial-gradient(circle at 40% 40%, #e2b24a 0%, #a8392a 45%, #5e1b17 100%); box-shadow: 0 0 10px rgba(255,255,255,.25); }

  .site-footer { position: absolute; left: 0; top: 960px; width: 731px; height: 240px; background: var(--red); }
  .call-box { position: absolute; left: 68px; top: 885px; width: 594px; height: 185px; border: 2px solid var(--white); background: linear-gradient(160deg, #3a2a26, #241c1a); }
  .call-kicker { position: absolute; left: 0; width: 100%; top: 30px; text-align: center; color: var(--red); font-size: 14px; font-weight: 600; }
  .call-title { position: absolute; left: 0; width: 100%; top: 44px; text-align: center; font-size: 25px; font-weight: 700; }
  .call-text { position: absolute; left: 0; width: 100%; top: 83px; text-align: center; font-family: "Arimo", sans-serif; font-size: 8px; line-height: 16px; }
  .phone-icon { position: absolute; left: 195px; top: 127px; width: 34px; height: 34px; border-radius: 50%; background: var(--white); display: flex; align-items: center; justify-content: center; }
  .phone-number { position: absolute; left: 238px; top: 128px; font-size: 23px; font-weight: 700; }
  .footer-nav a { position: absolute; top: 1110px; font-size: 11px; font-weight: 600; color: var(--white); text-decoration: none; }
  .copyright { position: absolute; left: 0; width: 731px; top: 1135px; text-align: center; font-family: "Arimo", sans-serif; font-size: 8px; line-height: 16px; }
  .can-art { position: absolute; left: 14px; top: 1088px; width: 76px; height: 100px; border-radius: 4px; background: linear-gradient(90deg, #5a66cc, #8a96e8); }
  .square-pizza-art { position: absolute; left: 599px; top: 1044px; width: 116px; height: 89px; border-radius: 4px; background: radial-gradient(circle, #e9b96a 0%, #c9773d 70%, #9a5428 100%); }
</style>
</head>
<body>
  <header class="site-header">
    <div class="brand"><span class="brand-mark"></span>Lantern Hollow</div>
    <nav class="main-nav">
      <a style="left:232px">THE KITCHEN</a>
      <a style="left:297px">OUR BEERS</a>
      <a style="left:354px">VISIT US</a>
      <a style="left:400px">ABOUT US</a>
      <a style="left:453px">MERCH</a>
      <span class="takeaway-icon"></span>
      <a style="left:518px">TAKE AWAY</a>
    </nav>
    <div class="btn-order-head">ORDER ONLINE</div>
  </header>

  <section class="hero">
    <div class="abs" style="inset:0" role="img" aria-label="Photo of square pizza and glasses of beer on a red wooden table"></div>
    <div class="hero-shade"></div>
    <h1 class="hero-title">SQUARE PIZZA AND GREAT BEER<br>IN PORTLAND, MAINE</h1>
    <div class="hero-btn" style="left:144px">ORDER PIZZA</div>
    <div class="hero-btn" style="left:256px">VISIT US</div>
    <div class="hero-btn" style="left:370px">OUR BEERS</div>
    <div class="hero-btn" style="left:482px">ABOUT US</div>
    <div class="hero-arrow" style="left:22px">
      <svg width="24" height="24" viewBox="0 0 24 24"><path d="M14 7 L9 12 L14 17" fill="none" stroke="#141414" stroke-width="2.2" stroke-linecap="round"/></svg>
    </div>
    <div class="hero-arrow" style="left:672px">
      <svg width="24" height="24" viewBox="0 0 24 24"><path d="M10 7 L15 12 L10 17" fill="none" stroke="#141414" stroke-width="2.2" stroke-linecap="round"/></svg>
    </div>
    <div class="promo-badge" role="img" aria-label="Promotional starburst badge reading Try Emberly"></div>
  </section>

  <svg class="abs" style="left:0;top:435px;z-index:1" width="731" height="35" viewBox="0 0 731 35">
    <polygon points="0,6 731,30 731,35 0,35" fill="var(--dark)"/>
    <polygon points="0,6 731,25 731,30 0,16" fill="var(--red)"/>
  </svg>

  <section class="intro">
    <div class="pattern-area" style="left:582px;top:65px;width:146px;height:80px" role="img" aria-label="Decorative dot pattern"></div>
    <div class="pattern-area" style="left:0;top:305px;width:123px;height:80px" role="img" aria-label="Decorative dot pattern"></div>
  </section>
  <h2 class="intro-title">WHAT IS <em>DETROIT-STYLE<br>PIZZA?</em></h2>
  <p class="intro-text">Lorem ipsum dolor sit amet, consectetur adipiscingincididunt ut labore et dolore magna aliqua. Ut enim ad minim veniam, quis nostrud exercitation ullamco laboris nisi ut aliquip ex ea commodo consequat. Duis aute irure dolor in reprehenderit in voluptate velit esse</p>
  <div class="btn btn-solid">ORDER ONLINE</div>
  <div class="btn btn-ghost">VIEW FULL MENU</div>
  <div class="pizza-photo" role="img" aria-label="Photo of a Detroit-style pepperoni pizza on a cooling rack"></div>

  <footer class="site-footer"></footer>
  <div class="call-box">
    <div class="call-kicker">QUESTIONS?</div>
    <div class="call-title">GIVE US A CALL</div>
    <p class="call-text">Lorem ipsum dolor sit amet, consectetur adipiscing elit, sed do eiusmod tempor incididunt ut labore et dolore magna aliqua.<br>Ut enim ad minim veniam, quis nostrud exercitation ullamco laboris nisi ut</p>
    <div class="phone-icon">
      <svg width="18" height="18" viewBox="0 0 24 24"><path d="M6.6 3.5 L9.5 3 L11 7.5 L8.8 9 C9.8 11.3 12.4 14 15 15.2 L16.5 13 L21 14.5 L20.5 17.4 C20 19.5 17.5 20.5 15 19.5 C10 17.5 6.5 14 4.5 9 C3.5 6.5 4.5 4 6.6 3.5 Z" fill="none" stroke="var(--red)" stroke-width="1.3"/></svg>
    </div>
    <div class="phone-number">+1 888 888 8888</div>
  </div>
  <nav class="footer-nav">
    <a style="left:196px">THE KITCHEN</a>
    <a style="left:284px">OUR BEERS</a>
    <a style="left:363px">VISIT US</a>
    <a style="left:426px">ABOUT US</a>
    <a style="left:500px">MERCH</a>
  </nav>
  <p class="copyright">© 2022 Lantern Hollow Brewing Company I This website is intended<br>for individuals of legal drinking age only.</p>
  <div class="can-art" role="img" aria-label="Illustration of a blue beer can"></div>
  <div class="square-pizza-art" role="img" aria-label="Illustration of a square pizza with toppings"></div>
</body>
</html>
```